Request for Business Card Design

Hi. My name is Marlene, I am looking for a new business card design for my company, Quarrow Signal Instruments, LLC. I really like the design you did for Tarsel Venture and was hoping you could do something similar using our full logo and our mark. I am also open to any raised texture design using our mark. I have attached our full logo, which would need to be somewhere on the card, as well as the mark in both outline and full form, as well as our brand colors / guide. The card does not have to be white, as long as our logo and mark appear. I actually like darker colored business cards more, but am open to all options. If you are interested in working with me, please let me know. We would also take the business card design into letterhead design if you can do that.

```html
<!DOCTYPE html>
<html lang="en">
<head>
<meta charset="utf-8">
<title>Quarrow Signal Instruments – Business Card</title>
<link href="https://fonts.googleapis.com/css2?family=Montserrat:wght@400;500;700&display=swap" rel="stylesheet">
<style>
  :root {
    --stage: #3a3330;
    --paper: #ffffff;
    --ink: #2b2d30;
    --brand-blue: #1a9ac3;
    --card-dark: #1b1c1e;
    --band-dark: #2d2f33;
    --muted: #55585d;
  }
  * { box-sizing: border-box; margin: 0; padding: 0; }
  html, body {
    width: 1200px; height: 786px; overflow: hidden;
    background: var(--stage);
    font-family: "Montserrat", Arial, sans-serif;
  }
  .stage {
    position: relative; width: 1200px; height: 786px;
    display: flex; align-items: center; justify-content: center; gap: 40px;
  }
  .card {
    position: relative; width: 540px; height: 310px; overflow: hidden;
    box-shadow: 0 10px 30px rgba(0,0,0,.45);
  }
  .card--front { background: var(--paper); color: var(--ink); }
  .card--back { background: var(--card-dark); }

  .wordmark { position: absolute; display: flex; align-items: center; gap: 10px; }
  .wordmark__dot { width: 30px; height: 30px; border-radius: 50%; background: var(--brand-blue); flex: none; }
  .wordmark__text { font-weight: 700; font-size: 27px; letter-spacing: 2px; line-height: 1; }
  .wordmark__sub { display: block; font-size: 7.5px; letter-spacing: .8px; margin-top: 4px; font-weight: 700; }
  .card--front .wordmark { top: 40px; left: 270px; }
  .card--front .wordmark__text { color: var(--ink); }
  .card--back .wordmark { top: 138px; right: 42px; }
  .card--back .wordmark__text { color: #ffffff; }

  .rule { position: absolute; left: 150px; top: 186px; width: 330px; height: 1.5px; background: var(--brand-blue); }
  .person { position: absolute; left: 30px; top: 160px; }
  .person__name { font-weight: 700; font-size: 24px; color: var(--brand-blue); }
  .person__role { font-size: 12px; color: var(--muted); margin-top: 1px; }

  .contacts { position: absolute; left: 30px; top: 218px; list-style: none; font-size: 12.5px; color: var(--ink); }
  .contacts li { display: flex; align-items: center; gap: 9px; height: 18px; }
  .contacts svg { width: 11px; height: 11px; fill: var(--brand-blue); flex: none; }

  .address { position: absolute; right: 40px; top: 232px; font-size: 12.5px; line-height: 1.4; color: var(--ink); }

  .bands { position: absolute; left: 0; bottom: 0; width: 540px; height: 24px; }
</style>
</head>
<body>
<main class="stage">
  <section class="card card--front" aria-label="Business card front">
    <div class="wordmark">
      <span class="wordmark__dot"></span>
      <div class="wordmark__text">QUARROW<span class="wordmark__sub">SIGNAL INSTRUMENTS</span></div>
    </div>

    <div class="person">
      <h1 class="person__name">Dorian Vale</h1>
      <p class="person__role">Owner</p>
    </div>
    <div class="rule"></div>

    <ul class="contacts">
      <li><svg viewBox="0 0 12 12"><path d="M2 1h3l1 3-1.5 1a7 7 0 0 0 2.5 2.5L8 6l3 1v3a1 1 0 0 1-1 1A9 9 0 0 1 1 2a1 1 0 0 1 1-1z"/></svg>+001 303 555 0148</li>
      <li><svg viewBox="0 0 12 12"><path d="M0 2h12v1L6 7 0 3zM0 4.5l6 4 6-4V10H0z"/></svg>info@quarrowsignal.com</li>
      <li><svg viewBox="0 0 12 12"><circle cx="6" cy="6" r="5.5"/></svg>www.quarrowsignal.com</li>
    </ul>

    <p class="address">1180 Harbor Field Road<br>Marlow, CO 80217</p>

    <svg class="bands" viewBox="0 0 540 24" aria-hidden="true">
      <polygon points="0,12 392,12 385,24 0,24" fill="var(--brand-blue)"/>
      <polygon points="408,0 540,0 540,24 396,24" fill="var(--band-dark)"/>
    </svg>
  </section>

  <section class="card card--back" aria-label="Business card back">
    <div class="wordmark">
      <span class="wordmark__dot"></span>
      <div class="wordmark__text">QUARROW<span class="wordmark__sub">SIGNAL INSTRUMENTS</span></div>
    </div>
  </section>
</main>
</body>
</html>
```